Business Card for a mobile physiotherapy company

I need a layout for a business card for a mobile physiotherapy company.
Slogan is "Mobile Physiotherapy - Your Road To Recovery"
Phone number is 867-555-0142
Email VardenTherapy@postnest.ca (subject to change with website)
Website www.VardenTherapy.ca
My name and credentials: Luke Varden Luke Varden, BSc(kin), MPT, CAFCI, IMS
Information maybe included: Direct Billing, Services including Physiotherapy, IMS, acupuncture
Maybe include facebook and instagram logos
One side with the logo clean and sharp
Other side with details, try not to look too busy, keep everything concise

```html
<!DOCTYPE html>
<html lang="en">
<head>
<meta charset="utf-8">
<title>Varden Therapy – Business Card</title>
<link rel="stylesheet" href="https://fonts.googleapis.com/css2?family=Source+Sans+3:wght@400;700&family=Tinos:wght@700&display=swap">
<style>
  :root {
    --navy: #2c4770;
    --green: #0b5445;
    --white: #ffffff;
    --ink: #1f2a33;
    --card-edge: #9a9c9f;
    --bg-light: #e7e8e9;
    --bg-dark: #b5b6b8;
    --rule: #c9cacc;
  }
  * { box-sizing: border-box; margin: 0; padding: 0; }
  html, body { width: 1200px; height: 1112px; overflow: hidden; }
  body {
    position: relative;
    background: linear-gradient(90deg, var(--bg-light) 0%, var(--bg-dark) 100%);
    font-family: "Source Sans 3", "Helvetica Neue", Arial, sans-serif;
  }
  .card {
    position: absolute;
    width: 767px;
    height: 438px;
    background: var(--white);
    border: 1px solid var(--card-edge);
    border-radius: 28px;
    overflow: hidden;
  }
  .card--front { left: 361px; top: 82px; }
  .card--back { left: 63px; top: 566px; }

  /* Brand name placeholder: plain text in the piece's own text font */
  .brand {
    position: absolute;
    text-align: center;
    color: var(--navy);
    font-family: "Source Sans 3", "Helvetica Neue", Arial, sans-serif;
    font-weight: 700;
    line-height: 1;
  }
  .brand--front { left: 40px; top: 150px; width: 330px; font-size: 40px; }
  .brand--back { left: 0; top: 150px; width: 767px; font-size: 80px; }

  .divider {
    position: absolute;
    left: 405px;
    top: 38px;
    width: 2px;
    height: 257px;
    background: var(--rule);
  }

  .details { position: absolute; left: 439px; top: 32px; color: var(--ink); }
  .details__name {
    font-family: "Tinos", "Times New Roman", serif;
    font-weight: 700;
    font-size: 26px;
    letter-spacing: 1px;
    color: var(--navy);
    text-transform: uppercase;
    line-height: 1;
  }
  .details__creds { font-size: 15px; margin-top: 8px; }
  .contact { list-style: none; margin-top: 14px; }
  .contact li { display: flex; align-items: center; gap: 7px; font-size: 18.5px; height: 32px; }
  .contact svg { width: 17px; height: 17px; flex: none; }
  .services__title { font-size: 19.5px; font-weight: 700; color: var(--navy); margin-top: 16px; line-height: 1.2; }
  .services__list { list-style: none; margin-top: 4px; color: var(--green); font-size: 18.5px; line-height: 1.5; }
  .services__row { display: flex; gap: 12px; }
  .services__row span::before { content: "•"; margin-right: 5px; font-size: 14px; vertical-align: 2px; }

  .wave { position: absolute; left: 0; top: 0; width: 767px; height: 438px; }
  .slogan {
    position: absolute;
    left: 0; right: 0;
    top: 397px;
    text-align: center;
    color: var(--white);
    font-family: "Tinos", "Times New Roman", serif;
    font-weight: 700;
    font-size: 21px;
  }

  .socials {
    position: absolute;
    left: 0; right: 0;
    top: 378px;
    display: flex;
    justify-content: center;
    gap: 26px;
    font-size: 22px;
    color: var(--ink);
  }
  .social { display: flex; align-items: center; gap: 10px; }
  .social__mark { width: 48px; height: 48px; border-radius: 5px; background: var(--navy); }
  .social__mark--alt { background: var(--green); }
</style>
</head>
<body>

<section class="card card--front">
  <svg class="wave" viewBox="0 0 767 438" aria-hidden="true">
    <path d="M0 282 C 190 340 430 380 640 379 C 430 378 190 336 0 302 Z" fill="var(--green)"/>
    <path d="M0 315 C 220 385 480 402 767 361 L767 438 L0 438 Z" fill="var(--navy)"/>
  </svg>

  <p class="brand brand--front">Varden Therapy</p>

  <div class="divider"></div>

  <div class="details">
    <h1 class="details__name">Luke Varden</h1>
    <p class="details__creds">BSc(kin), MPT, CAFCI, IMS</p>
    <ul class="contact">
      <li>
        <svg viewBox="0 0 20 20" aria-hidden="true"><circle cx="10" cy="10" r="8.6" fill="none" stroke="var(--navy)" stroke-width="1.8"/><path d="M7 5.5 L8.6 7.6 L7.8 8.8 C8.4 10 9.6 11.4 11 12 L12.2 11.2 L14.3 12.8 L13.2 14.3 C10 14 6.2 10.2 5.8 7 Z" fill="var(--navy)"/></svg>
        <span>867-555-0142</span>
      </li>
      <li>
        <svg viewBox="0 0 20 20" aria-hidden="true"><circle cx="10" cy="10" r="8.6" fill="none" stroke="var(--navy)" stroke-width="1.8"/><rect x="5.5" y="7" width="9" height="6.5" rx="1" fill="var(--navy)"/><path d="M5.8 7.4 L10 10.6 L14.2 7.4" fill="none" stroke="var(--white)" stroke-width="1.1"/></svg>
        <span>VardenTherapy@postnest.ca</span>
      </li>
      <li>
        <svg viewBox="0 0 20 20" aria-hidden="true"><g fill="none" stroke="var(--navy)" stroke-width="1.4"><circle cx="10" cy="10" r="8.4"/><ellipse cx="10" cy="10" rx="3.6" ry="8.4"/><path d="M1.8 10 H18.2 M3.2 5.8 H16.8 M3.2 14.2 H16.8"/></g></svg>
        <span>www.VardenTherapy.ca</span>
      </li>
    </ul>
    <h2 class="services__title">Services Including</h2>
    <div class="services__list">
      <p class="services__row"><span>Physiotherapy</span><span>Direct Billing</span></p>
      <p class="services__row"><span>Ims</span><span>Acupuncture</span></p>
    </div>
  </div>

  <p class="slogan">Mobile Physiotherapy - Your Road To Recovery</p>
</section>

<section class="card card--back">
  <p class="brand brand--back">Varden Therapy</p>
  <div class="socials">
    <div class="social"><span class="social__mark"></span><span>VardenTherapy</span></div>
    <div class="social"><span class="social__mark social__mark--alt"></span><span>@VardenTherapy</span></div>
  </div>
</section>

</body>
</html>
```